Kauri Crest Builders Business Card Design

We need a business card for an established builder of high quality bespoke homes in Auckland and Northland. We build and renovate homes collaboratively facilitating effective communication between owners, builders, architects, suppliers and tradespeople. We have never built or renovated a home that leaks or has faults. We only use reliable materials. We have never been sued or had legal action taken against us. We are honest builders of bespoke homes not group mass produced homes. Our niche market is in character homes. We practice sustainability and have built a lot of coastal property. We have been in business for over thirty years . We would like to see natural colors of the environment sand,sea and maybe vegetation . The design should communicate quality, sustainability,fair pricing, open communication and the originality of bespoke building. And the fact that the builder is registered.

Industry/Entity Type

Business

Contact Information for Business Card

Rowan Tellick Builders
Ph. 021583917
18 Kestrel Rd Harwood Bay Auckland 0814
PO Box 927 Mangawhai 0583

```html
<!DOCTYPE html>
<html lang="en">
<head>
<meta charset="utf-8">
<title>Kauri Crest Builders – Business Card</title>
<link rel="stylesheet" href="https://fonts.googleapis.com/css2?family=Open+Sans:wght@400;700&display=swap">
<style>
  :root {
    --page-bg: #3a332e;
    --card-black: #1c1c1d;
    --card-black-light: #2a2a2c;
    --brand-red: #c40d10;
    --text-white: #f2f2f2;
    --logo-grey: #d2d2d2;
  }
  * { margin: 0; padding: 0; box-sizing: border-box; }
  html, body {
    width: 1200px; height: 844px; overflow: hidden;
    background: var(--page-bg);
    font-family: "Open Sans", Arial, sans-serif;
  }
  .canvas {
    position: relative; width: 1200px; height: 844px;
    display: flex; align-items: center; justify-content: center; gap: 50px;
  }
  .card {
    position: relative; width: 510px; height: 300px;
    background: radial-gradient(circle at 60% 40%, var(--card-black-light), var(--card-black) 70%);
    box-shadow: 0 10px 30px rgba(0,0,0,.45);
    overflow: hidden;
  }
  /* Back: contact side */
  .card-back .band {
    position: absolute; left: 0; right: 0; height: 14px; background: var(--brand-red);
  }
  .card-back .band-top { top: 0; }
  .card-back .band-bottom { bottom: 0; }
  .contact {
    position: absolute; inset: 0; text-align: center; color: var(--text-white);
    padding-top: 78px; font-size: 15px; line-height: 1.3;
  }
  .contact-name {
    color: var(--brand-red); font-size: 18px; font-weight: 400;
    letter-spacing: .5px; text-transform: uppercase; margin-bottom: 36px;
  }
  .contact-phone { margin-bottom: 42px; }
  /* Front: brand side */
  .tab {
    position: absolute; width: 22px; height: 42px; background: var(--brand-red);
    border-right: 4px solid var(--text-white);
  }
  .tab-left { left: 0; top: 140px; }
  .tab-right { right: 0; top: 22px; border-right: none; border-left: 4px solid var(--text-white); }
  .brand {
    position: absolute; inset: 0; display: flex; align-items: center; justify-content: center; gap: 12px;
  }
  .brand-mark { width: 16px; height: 16px; background: var(--brand-red); }
  .brand-name {
    color: var(--logo-grey); font-weight: 700; font-size: 34px; letter-spacing: -.5px;
  }
</style>
</head>
<body>
  <main class="canvas">
    <section class="card card-back" aria-label="Business card back">
      <div class="band band-top"></div>
      <div class="contact">
        <h1 class="contact-name">Rowan Tellick Builders</h1>
        <p class="contact-phone">021583917</p>
        <p class="contact-address">18 Kestrel Rd Harwood Bay<br>Auckland 0814<br>PO Box 927 Mangawhai 0583</p>
      </div>
      <div class="band band-bottom"></div>
    </section>
    <section class="card card-front" aria-label="Business card front">
      <div class="tab tab-right"></div>
      <div class="tab tab-left"></div>
      <div class="brand">
        <span class="brand-mark"></span>
        <span class="brand-name">Kauri Crest Builders</span>
      </div>
    </section>
  </main>
</body>
</html>
```